Harborlight Amusement Collective (HAC)

We need a business card design for Harborlight Amusement Collective. Modern and sleek looking, with all critical information. Open to single or double sided designs, if double sided info needs to be all on one side. The main Logo is Harborlight Amusement collective and must be on the card. The other three logos are for the brands that fall under the group, they might be good on the back.

Industry/Entity Type

Business

```html
<!DOCTYPE html>
<html lang="en">
<head>
<meta charset="utf-8">
<title>Harborlight Amusement Collective – Business Card</title>
<link href="https://fonts.googleapis.com/css2?family=Montserrat:wght@400;500;600;700&display=swap" rel="stylesheet">
<style>
  :root {
    --blue: #2456a4;
    --green: #8bab2f;
    --ink: #2b2b2b;
    --muted: #555;
    --card: #ffffff;
    --bg: #e4e4e4;
    --faint: #eeeff1;
  }
  * { box-sizing: border-box; margin: 0; padding: 0; }
  html, body { width: 1200px; height: 852px; overflow: hidden; }
  body {
    background: var(--bg);
    font-family: "Montserrat", Arial, sans-serif;
    color: var(--ink);
    position: relative;
  }
  .card {
    position: absolute;
    width: 540px;
    height: 310px;
    background: var(--card);
    border-radius: 22px;
    overflow: hidden;
    box-shadow: 0 2px 6px rgba(0,0,0,.12);
  }
  .card--front { left: 40px; top: 271px; }
  .card--back { left: 620px; top: 271px; }

  /* wordmark */
  .wordmark { display: flex; align-items: center; gap: 10px; }
  .wordmark__square { width: 22px; height: 22px; background: var(--green); flex: none; }
  .wordmark__name {
    color: var(--blue);
    font-weight: 700;
    font-size: 19px;
    line-height: 1.15;
    letter-spacing: .3px;
    text-transform: uppercase;
  }

  /* front */
  .front__logo { position: absolute; top: 44px; left: 0; right: 0; display: flex; justify-content: center; }
  .front__logo .wordmark__name { text-align: left; }
  .rule { position: absolute; height: 2px; background: var(--green); }
  .rule--blue { background: var(--blue); }
  .front__label {
    position: absolute; top: 148px; left: 0; right: 0;
    text-align: center; font-size: 12px; color: var(--muted);
  }
  .brands {
    position: absolute; top: 174px; left: 30px; right: 30px;
    display: flex; justify-content: space-between; align-items: center;
  }
  .brand { display: flex; align-items: center; gap: 7px; font-weight: 700; font-size: 17px; }
  .brand__dot { width: 14px; height: 14px; border-radius: 50%; flex: none; }
  .brand--tix { color: var(--green); }
  .brand--tix .brand__dot { background: var(--green); }
  .brand--host { color: var(--ink); }
  .brand--host .brand__dot { background: var(--ink); }
  .brand--gate { color: var(--blue); }
  .brand--gate .brand__dot { background: var(--blue); }
  .brand__divider { width: 1px; height: 36px; background: #9a9a9a; }
  .front__web {
    position: absolute; top: 248px; left: 0; right: 0;
    text-align: center; font-size: 13px; color: var(--ink);
  }
  .front__web span { color: var(--blue); }

  /* back */
  .back__pattern {
    position: absolute; right: 0; top: 0; width: 250px; height: 230px;
    background: linear-gradient(135deg, var(--faint), #fafafa);
  }
  .back__logo { position: absolute; left: 30px; top: 120px; width: 220px; }
  .back__contact { position: absolute; left: 290px; top: 42px; }
  .contact__name { color: var(--blue); font-weight: 700; font-size: 19px; }
  .contact__title { font-size: 12px; color: var(--ink); margin-top: 2px; }
  .contact__address { font-size: 12.5px; margin-top: 16px; line-height: 1.35; }
  .contact__list { list-style: none; margin-top: 10px; font-size: 12.5px; }
  .contact__list li { display: flex; align-items: center; gap: 8px; height: 19px; }
  .contact__list svg { width: 13px; height: 13px; fill: var(--blue); flex: none; }
  .contact__list .link { color: var(--blue); }
  .back__band {
    position: absolute; left: 0; bottom: 0; width: 100%; height: 14px; background: var(--green);
  }
  .back__tab {
    position: absolute; right: 0; bottom: 0; width: 275px; height: 62px;
    background: var(--blue); border-top-left-radius: 20px;
    color: #fff; font-size: 12.5px; display: flex; align-items: center; justify-content: center;
  }
</style>
</head>
<body>

  <section class="card card--front">
    <div class="front__logo">
      <div class="wordmark">
        <span class="wordmark__square"></span>
        <span class="wordmark__name">Harborlight<br>Amusement Collective</span>
      </div>
    </div>
    <span class="rule" style="left:60px; right:60px; top:126px;"></span>
    <p class="front__label">Our Brands</p>
    <div class="brands">
      <div class="brand brand--tix"><span class="brand__dot"></span>HarborTix</div>
      <span class="brand__divider"></span>
      <div class="brand brand--host"><span class="brand__dot"></span>Bleacherline Hosting</div>
      <span class="brand__divider"></span>
      <div class="brand brand--gate"><span class="brand__dot"></span>Gatewise</div>
    </div>
    <span class="rule" style="left:60px; right:60px; top:232px;"></span>
    <p class="front__web">www.<span>harborlightcollective</span>.com</p>
    <span class="rule rule--blue" style="left:90px; width:60px; top:257px;"></span>
    <span class="rule rule--blue" style="right:90px; width:60px; top:257px;"></span>
  </section>

  <section class="card card--back">
    <div class="back__pattern" role="img" aria-label="Faint large brand emblem watermark"></div>
    <div class="back__logo">
      <div class="wordmark">
        <span class="wordmark__square"></span>
        <span class="wordmark__name" style="font-size:16px;">Harborlight<br>Amusement Collective</span>
      </div>
    </div>
    <div class="back__contact">
      <h1 class="contact__name">Rowan Ellery Vance</h1>
      <p class="contact__title">Managing Director</p>
      <p class="contact__address">58 Quayside Rd.,<br>Port Town, US 204811</p>
      <ul class="contact__list">
        <li><svg viewBox="0 0 24 24"><path d="M6.6 10.8a15 15 0 0 0 6.6 6.6l2.2-2.2c.3-.3.7-.4 1-.2 1.1.4 2.3.6 3.6.6.6 0 1 .4 1 1V20c0 .6-.4 1-1 1A17 17 0 0 1 3 4c0-.6.4-1 1-1h3.5c.6 0 1 .4 1 1 0 1.3.2 2.5.6 3.6.1.3 0 .7-.2 1z"/></svg>555.210.4477</li>
        <li><svg viewBox="0 0 24 24"><path d="M2 5h20v14H2zm2 2v.5l8 5 8-5V7zm0 2.8V17h16V9.8l-8 5z"/></svg>rowan@harborlightcollective.com</li>
        <li><svg viewBox="0 0 24 24"><path d="M12 2a10 10 0 1 0 0 20 10 10 0 0 0 0-20zm6.9 6h-3a15 15 0 0 0-1.3-3.9A8 8 0 0 1 18.9 8zM12 4c.8 1.2 1.5 2.5 1.9 4h-3.8c.4-1.5 1.1-2.8 1.9-4zM4.3 14a8 8 0 0 1 0-4h3.4a16 16 0 0 0 0 4zm.8 2h3a15 15 0 0 0 1.3 3.9A8 8 0 0 1 5.1 16zm3-8h-3a8 8 0 0 1 4.3-3.9C8.8 5.3 8.4 6.6 8.1 8zM12 20c-.8-1.2-1.5-2.5-1.9-4h3.8c-.4 1.5-1.1 2.8-1.9 4zm2.3-6H9.7a14 14 0 0 1 0-4h4.6a14 14 0 0 1 0 4zm.3 5.9c.6-1.2 1-2.5 1.3-3.9h3a8 8 0 0 1-4.3 3.9zm1.7-5.9a16 16 0 0 0 0-4h3.4a8 8 0 0 1 0 4z"/></svg><span>www.<span class="link">harborlightcollective</span>.com</span></li>
      </ul>
    </div>
    <div class="back__band"></div>
    <div class="back__tab">Harborlight Amusement Collective Ltd</div>
  </section>

</body>
</html>
```